Fun, Clean Business Card For Family Focused Travel Agency

I need a business card using specific colors and fonts as in the uploaded files. Ideally, I would like a large image of the logo on the back and all the contact info on the front. Maybe the stars/dots somewhere in a flowy form.

I do want it the contact information to be clear and easy to read. I don't want it to look too busy. Maybe even a bit minimalist.

I plan or ordering the ROUNDED CORNER business cards from Cardwell Press, so please consider that in your design.

Target Market(s)

Families with children, couples, groups of friends

Contact Information for Business Card

Marla Quint, Owner
Marla@TumbleTrips.example
Cell Phone Number 555-218-4603
Office Phone Number 555-647-1925
Specializing in Glimmerland destinations, Pelican Bay Fun Park, Cruises and All-Inclusive Vacations.

Nice but not required:
www.TumbleTrips.example
Facebook, Instagram, Twitter icons with username: TumbleTrips

Font styles to use
Sans Serif

Requirements
Must have
• Please try to use the colors from the logo as much as possible. I understand lighter shades/colors may be needed for some things.
Should not have
• NO SERIF FONTS. That is really the only thing I do not want at all

```html
<!DOCTYPE html>
<html lang="en">
<head>
<meta charset="utf-8">
<title>TumbleTrips Business Card</title>
<link href="https://fonts.googleapis.com/css2?family=Work+Sans:wght@400;500;600&display=swap" rel="stylesheet">
<style>
  :root {
    --stage: #1d1d20;
    --card-navy: #141a33;
    --card-navy-deep: #10152b;
    --accent-orange: #ee7d2b;
    --text-white: #f4f5f8;
    --foil-silver: #c8cad2;
    --muted: #d9dbe3;
  }
  * { margin: 0; padding: 0; box-sizing: border-box; }
  html, body { width: 1200px; height: 900px; overflow: hidden; }
  body {
    background: var(--stage);
    font-family: "Work Sans", Arial, sans-serif;
    color: var(--text-white);
    position: relative;
  }
  .card {
    position: absolute;
    left: 290px;
    width: 620px;
    height: 354px;
    border-radius: 18px;
    background: linear-gradient(160deg, var(--card-navy) 0%, var(--card-navy-deep) 100%);
  }
  .card-back { top: 72px; }
  .card-front { top: 474px; }

  /* Back */
  .back-brand {
    position: absolute;
    top: 108px;
    left: 0; right: 0;
    display: flex;
    align-items: center;
    justify-content: center;
    gap: 16px;
  }
  .brand-dot {
    width: 54px; height: 54px;
    border-radius: 50%;
    background: var(--foil-silver);
  }
  .back-brand .brand-name {
    font-size: 52px;
    font-weight: 600;
    color: var(--foil-silver);
    letter-spacing: 0.5px;
  }
  .tagline {
    position: absolute;
    top: 232px;
    left: 60px; right: 60px;
    text-align: center;
    font-size: 15px;
    line-height: 1.4;
    letter-spacing: 0.6px;
    color: var(--text-white);
  }

  /* Front */
  .front-brand {
    position: absolute;
    top: 140px;
    left: 40px;
    display: flex;
    align-items: center;
    gap: 12px;
  }
  .front-brand .brand-dot {
    width: 48px; height: 48px;
    background: var(--text-white);
  }
  .front-brand .brand-name {
    font-size: 38px;
    font-weight: 600;
    color: var(--text-white);
  }
  .divider {
    position: absolute;
    left: 330px;
    top: 90px;
    width: 2px;
    height: 180px;
    background: var(--accent-orange);
  }
  .contact {
    position: absolute;
    left: 356px;
    top: 92px;
  }
  .person-name {
    font-size: 29px;
    font-weight: 500;
    letter-spacing: 2.5px;
    color: var(--accent-orange);
    text-transform: uppercase;
    line-height: 1;
  }
  .person-role {
    font-size: 15px;
    letter-spacing: 0.6px;
    margin: 4px 0 14px;
  }
  .contact-list { list-style: none; }
  .contact-list li {
    display: flex;
    align-items: center;
    gap: 10px;
    font-size: 16px;
    letter-spacing: 0.6px;
    line-height: 25px;
  }
  .contact-list svg { width: 12px; height: 12px; flex: none; }
  .social-handle {
    position: absolute;
    left: 356px;
    top: 296px;
    display: flex;
    align-items: center;
    gap: 12px;
    font-size: 18px;
    letter-spacing: 0.6px;
  }
  .handle-dot {
    width: 18px; height: 18px;
    border-radius: 50%;
    background: var(--accent-orange);
  }
</style>
</head>
<body>
  <section class="card card-back" aria-label="Card back">
    <div class="back-brand">
      <span class="brand-dot"></span>
      <span class="brand-name">TumbleTrips</span>
    </div>
    <p class="tagline">Specializing in Glimmerland destinations, Pelican Bay Fun Park,<br>Cruises and All-Inclusive Vacations.</p>
  </section>

  <section class="card card-front" aria-label="Card front">
    <div class="front-brand">
      <span class="brand-dot"></span>
      <span class="brand-name">TumbleTrips</span>
    </div>
    <div class="divider"></div>
    <div class="contact">
      <h1 class="person-name">Marla Quint</h1>
      <p class="person-role">Owner</p>
      <ul class="contact-list">
        <li>
          <svg viewBox="0 0 12 12" aria-hidden="true"><rect x="3" y="0.8" width="6" height="10.4" rx="1.2" fill="none" stroke="var(--accent-orange)" stroke-width="1.3"/><circle cx="6" cy="9.2" r="0.7" fill="var(--accent-orange)"/></svg>
          555-218-4603
        </li>
        <li>
          <svg viewBox="0 0 12 12" aria-hidden="true"><path d="M2.5 1 L4.5 1 L5.2 3.6 L4 4.6 C4.8 6.3 5.7 7.2 7.4 8 L8.4 6.8 L11 7.5 L11 9.5 C11 10.3 10.3 11 9.5 11 C5 10.6 1.4 7 1 2.5 C1 1.7 1.7 1 2.5 1 Z" fill="var(--accent-orange)"/></svg>
          555-647-1925
        </li>
        <li>
          <svg viewBox="0 0 12 12" aria-hidden="true"><rect x="0.8" y="2.3" width="10.4" height="7.4" rx="1" fill="none" stroke="var(--accent-orange)" stroke-width="1.2"/><path d="M1 2.8 L6 6.6 L11 2.8" fill="none" stroke="var(--accent-orange)" stroke-width="1.2"/></svg>
          Marla@TumbleTrips.example
        </li>
        <li>
          <svg viewBox="0 0 12 12" aria-hidden="true"><circle cx="6" cy="6" r="5" fill="none" stroke="var(--accent-orange)" stroke-width="1.1"/><ellipse cx="6" cy="6" rx="2.2" ry="5" fill="none" stroke="var(--accent-orange)" stroke-width="1"/><path d="M1 6 H11 M2 3.5 H10 M2 8.5 H10" stroke="var(--accent-orange)" stroke-width="0.9"/></svg>
          www.TumbleTrips.example
        </li>
      </ul>
    </div>
    <div class="social-handle">
      <span>TumbleTrips</span>
      <span class="handle-dot"></span>
    </div>
  </section>
</body>
</html>
```